Wordpress Design Project

I have a main site www.tinymolarclinic.example for 9 dental offices. I want a designed wordpress mini-site template that I can use to create mini sites for each location and related projects that keeps the look and feel of the home site.
Updates

I'm getting different designs from my original web site. Maybe I'm confusing the designers but to clarify:

what I want is to keep the same graphics as we already have on this site www.tinymolarclinic.example and just convert it to a Wordpress site template to be used as individual MINI sites. 

No new designs needed, same design just different platform.

Target Market(s)

see site www.tinymolarclinic.example

Industry/Entity Type

Dental

Requirements
Must have
• Can we make the Logo larger?
Should not have
• I think you're basing your designs on tinymolarclinicglendale.example but I specifically said it should be based on the home site which is www.tinymolarclinic.example
Please view the difference. I need for it to have the same APPEARANCE. Please!
http://www.tinymolarclinic.example/

```html
<!DOCTYPE html>
<html lang="en">
<head>
<meta charset="utf-8">
<title>Tiny Molar Clinic – Hollywood</title>
<link href="https://fonts.googleapis.com/css2?family=Ubuntu:wght@300;400;500&family=Fira+Sans+Extra+Condensed:wght@500;600&display=swap" rel="stylesheet">
<style>
:root{
  --red:#c8161d;
  --grey-head:#9b9b9b;
  --text:#444;
  --text-dark:#3a3a3a;
  --navy:#1f2a6b;
  --line:#d9d9d9;
  --bg:#f7f7f7;
  --btn-grey:#666;
  --logo-gold:#e2ad2a;
}
*{box-sizing:border-box;margin:0;padding:0}
html,body{width:1029px;height:1200px;overflow:hidden}
body{position:relative;background:linear-gradient(#f2f2f2 0,#fff 230px,#fff);font-family:"Ubuntu",sans-serif;color:var(--text)}
a{color:inherit;text-decoration:none}
.abs{position:absolute}
.top-rule{left:0;top:0;width:1029px;height:4px;background:#666}
.util-tab{left:712px;top:4px;width:206px;height:31px;background:#6a6a6a;border-radius:0 0 4px 4px;color:#fff;font-size:10px;display:flex;align-items:center;justify-content:center;gap:7px}
.brand{left:111px;top:16px;display:flex;align-items:center;gap:14px;font-size:30px;font-weight:500;color:var(--red)}
.brand-dot{width:104px;height:104px;border-radius:50%;background:var(--logo-gold);flex:none}
.contact-line{display:flex;align-items:center;gap:7px}
.icon-circ{width:21px;height:21px;border-radius:50%;background:#8a8a8a;display:flex;align-items:center;justify-content:center}
.email{left:667px;top:52px;font-size:10px;color:var(--red);text-decoration:underline}
.phone{left:667px;top:90px;font-size:19px;color:var(--red)}
.nav{left:111px;top:136px;width:806px;height:37px;border-top:3px solid #ddd;border-bottom:3px solid #ddd;background:#fff;display:flex}
.nav a{height:31px;display:flex;align-items:center;justify-content:center;font-size:13px;color:#222;border-right:1px solid #ddd}
.nav a.current{background:linear-gradient(#ececec,#c9c9c9)}
.nav a:last-child{border-right:0}
.hero{left:111px;top:178px;width:806px;height:330px;border:1px solid #ddd;background:#f1f1f3;overflow:hidden}
.hero-photo{position:absolute;left:0;top:0;width:481px;height:330px;background:radial-gradient(circle at 50% 40%,#f2cfae,#d9a97c 45%,#b58a5b 70%,#efe7c9)}
.hero-title{position:absolute;left:492px;top:64px;font-family:"Fira Sans Extra Condensed",sans-serif;font-weight:600;font-size:37px;line-height:41px;color:#4a4a4a}
.btn-red{background:var(--red);color:#fff;font-family:"Fira Sans Extra Condensed",sans-serif;font-weight:600;border:2px solid #fff;box-shadow:0 0 0 1px #ccc;border-radius:3px;display:flex;align-items:center;justify-content:center}
.hero-cta{position:absolute;left:493px;top:176px;width:205px;height:35px;font-size:20px}
.dots{position:absolute;left:714px;top:303px;display:flex;gap:3px}
.dots span{width:14px;height:14px;border-radius:50%;background:#aaa}
.dots span:first-child{background:#333}
.h2{font-family:"Fira Sans Extra Condensed",sans-serif;font-weight:600;color:var(--red);font-size:29px;line-height:30px}
.h2 span{color:var(--grey-head)}
.copy{font-size:10.5px;line-height:17px;font-weight:400;color:var(--text-dark)}
.welcome-h{left:111px;top:533px}
.welcome-p{left:111px;top:573px;width:530px}
.read-more{width:77px;height:28px;font-size:16px}
.rm1{left:564px;top:670px}
.divider{height:1px;background:var(--line)}
.d-main{left:111px;top:719px;width:532px}
.why-h{left:111px;top:740px}
.photo{background:linear-gradient(135deg,#e9eef3,#b7c6d4);border:1px solid #ddd;box-shadow:0 0 0 3px #fff,0 1px 4px rgba(0,0,0,.25)}
.why-img{left:113px;top:782px;width:186px;height:127px}
.why-p{left:317px;top:777px;width:322px}
.rm2{left:564px;top:927px}
.side-img{left:661px;width:118px;height:110px}
.side-h{left:797px;font-size:25px}
.side-p{left:797px;width:125px;font-size:10.5px;line-height:15.5px;font-weight:400;color:var(--text-dark)}
.btn-more{left:797px;width:52px;height:27px;background:var(--btn-grey);color:#fff;border-radius:3px;font-size:13px;font-weight:500;display:flex;align-items:center;justify-content:center}
.d-side{left:660px;width:258px}
.footer{left:0;top:982px;width:1029px;height:153px;background:var(--bg);border-top:4px solid #ddd}
.footer-inner{position:absolute;left:111px;top:0;width:806px;height:100%}
.foot-top{position:absolute;left:0;top:22px;font-size:12px;color:var(--navy);display:flex;gap:10px}
.foot-list{position:absolute;top:55px;list-style:none;font-size:10.5px;color:#555;font-weight:400}
.foot-list li{height:24.5px;display:flex;align-items:flex-start;gap:10px}
.foot-list li::before{content:"";width:5px;height:7px;margin-top:3px;background:var(--red)}
.foot-h{position:absolute;top:22px;font-size:14.5px;color:var(--navy);font-weight:500}
.addr{position:absolute;left:483px;top:50px;font-size:10.5px;line-height:17px;font-weight:400;color:#444;font-style:normal}
.addr strong{font-weight:500;color:#222}
.addr .tel{color:var(--red)}
.social{position:absolute;left:686px;top:48px;list-style:none;font-size:10.5px;font-weight:400;color:#444}
.social li{height:26px;display:flex;align-items:center;gap:8px}
.social i{width:13px;height:13px;border-radius:2px;display:block}
.copyright{left:0;top:1158px;width:1029px;text-align:center;font-size:10.5px;font-weight:400;color:#666}
.bottom-line{left:0;top:1135px;width:1029px;height:1px;background:#e2e2e2}
</style>
</head>
<body>
<div class="abs top-rule"></div>
<nav class="abs util-tab"><a href="#">Patients Login</a>|<a href="#">Location</a>|<a href="#">Site Map</a></nav>

<a class="abs brand" href="#"><span class="brand-dot"></span>Tiny Molar Clinic</a>

<div class="abs contact-line email">
  <span class="icon-circ"><svg width="11" height="8" viewBox="0 0 11 8"><rect x=".5" y=".5" width="10" height="7" fill="none" stroke="#fff"/><path d="M.5 .5 5.5 4.5 10.5 .5" fill="none" stroke="#fff"/></svg></span>
  <a href="#">hollywood@tinymolarclinic.example</a>
</div>
<div class="abs contact-line phone">
  <span class="icon-circ"><svg width="11" height="11" viewBox="0 0 12 12"><path d="M2 1l2 0 1 3-1.5 1a7 7 0 0 0 3.5 3.5L8 7l3 1v2a1 1 0 0 1-1 1A9 9 0 0 1 1 2a1 1 0 0 1 1-1z" fill="#fff"/></svg></span>
  <span>1-888-555-0142</span>
</div>

<nav class="abs nav">
  <a class="current" href="#" style="width:86px">HOME</a>
  <a href="#" style="width:142px">OUR DENTAL CARE</a>
  <a href="#" style="width:117px">NEW PATIENTS</a>
  <a href="#" style="width:112px">APPOINTMENT</a>
  <a href="#" style="width:92px">ABOUT US</a>
  <a href="#" style="width:66px">BLOG</a>
  <a href="#" style="width:66px">FAQ’s</a>
  <a href="#" style="width:125px">CONTACT US</a>
</nav>

<section class="abs hero">
  <div class="hero-photo" role="img" aria-label="Photo of a young child brushing teeth with a pink toothbrush"></div>
  <h1 class="hero-title">Get The Dental Help<br>You Need Now! -</h1>
  <a class="btn-red hero-cta" href="#">Request An Appointment</a>
  <div class="dots"><span></span><span></span><span></span><span></span><span></span></div>
</section>

<h2 class="abs h2 welcome-h">Welcome to <span>Tinymolarclinic</span></h2>
<p class="abs copy welcome-p">Aliquam molestie, mi et imperdiet euismod, dui purus auctor tellus, et interdum lacus lectus et ante. Sed accumsan sollicitudin sapien, sit amet adipiscing turpis gravida ac. In congue, neque ac lobortis volutpat, libero mauris varius mi, vitae suscipit ipsum ligula vitae risus. Duis aliquam nibh a dui iaculis viverra id a velit. Vivamus egestas risus in magna varius commodo. Sed semper viverra egestas. Etiam pretium porttitor lectus, vel ornare neque porta volutpat.</p>
<a class="abs btn-red read-more rm1" href="#">Read More</a>
<div class="abs divider d-main"></div>

<h2 class="abs h2 why-h">Why <span>Tinymolarclinic</span></h2>
<div class="abs photo why-img" role="img" aria-label="Photo of a dentist examining a smiling patient"></div>
<p class="abs copy why-p">Aliquam molestie, mi et imperdiet euismod, dui purus auctor tellus, et interdum lacus lectus et ante. Sed accumsan sollicitudin sapien, sit amet adipiscing turpis gravida ac. In congue, neque ac lobortis volutpat, libero mauris varius mi, vitae suscipit ipsum ligula vitae risus. Duis aliquam nibh a dui iaculis viverra id a velit. Vivamus egestas risus in magna varius commodo. Sed semper viverra egestas. Etiam pretium porttitor lectus, vel ornare neque porta volutpat.</p>
<a class="abs btn-red read-more rm2" href="#">Read More</a>

<div class="abs photo side-img" style="top:539px" role="img" aria-label="Photo of the dental team at work"></div>
<h3 class="abs h2 side-h" style="top:537px">About <span>Team</span></h3>
<p class="abs side-p" style="top:568px">Get the scoop on our dentists and the great team ready to serve you.</p>
<a class="abs btn-more" style="top:624px" href="#">More</a>
<div class="abs divider d-side" style="top:672px"></div>

<div class="abs photo side-img" style="top:694px" role="img" aria-label="Photo of hands typing on a laptop keyboard"></div>
<h3 class="abs h2 side-h" style="top:692px">Our <span>Hours</span></h3>
<p class="abs side-p" style="top:725px;line-height:17px">We're open 9am to 6pm Monday-Saturday</p>
<a class="abs btn-more" style="top:779px" href="#">More</a>
<div class="abs divider d-side" style="top:827px"></div>

<div class="abs photo side-img" style="top:847px" role="img" aria-label="Photo of a smiling patient in the clinic"></div>
<h3 class="abs h2 side-h" style="top:844px">About <span>Patients</span></h3>
<p class="abs side-p" style="top:875px;line-height:17px">Save time and print the required new patient forms out now.</p>
<a class="abs btn-more" style="top:932px" href="#">More</a>

<footer class="abs footer">
  <div class="footer-inner">
    <nav class="foot-top"><a href="#">Home</a>|<a href="#">Contact Us</a>|<a href="#">Blog</a></nav>
    <ul class="foot-list" style="left:0"><li>About Us</li><li>Services</li><li>Testimonials</li></ul>
    <ul class="foot-list" style="left:138px"><li>Our Promise</li><li>Common Questions</li><li>Our Founder</li></ul>
    <ul class="foot-list" style="left:277px"><li>Request An Appointment</li><li>Directions</li><li>Office Info</li></ul>
    <h4 class="foot-h" style="left:483px">Location Address</h4>
    <address class="addr"><strong>Tiny Molar Clinic</strong><br>Hollywood<br>1200 Example Blvd<br>Los Angeles, CA 90000<br><span class="tel">(323) 555-0187</span></address>
    <h4 class="foot-h" style="left:686px">Contact Us</h4>
    <ul class="social">
      <li><i style="background:#3b5998"></i>Friendbook</li>
      <li><i style="background:#4fb6e0"></i>Chirper</li>
      <li><i style="background:#333"></i>Circles +</li>
      <li><i style="background:#f08a1d"></i>Rss</li>
    </ul>
  </div>
</footer>
<div class="abs bottom-line"></div>
<p class="abs copyright">© 2012 Tiny Molar Clinic &nbsp;| Privacy Policy | Sitemap</p>
</body>
</html>
```